High-end construction company needs a business card design

We need a modern looking business card that draws people in, is memorable and looks so good people will want to sick it on their fridges.
On the first side what is needed are:
Logo
My name - Tomasz Brelwik
Title - Managing Director
Website - www.varkelt.co.uk
Email - tomasz@varkelt.co.uk
Telephone - 020 5194 6281
Mobile - 07845139072
On the back side was is needed is a list of all the services we provide:
-Kitchen Renovations
-Bathroom Renovations
-House Renovations
-Garage Conversions
-Extensions
-Loft Conversions
-Conservatories
-Carpentry
-Tiling
-Electrical
-Plumbing & Heating
-Bricklaying
-Landscaping
-Decorating
-Plastering
We would like the colours to be the same shades as on the logo with grey or black for the words.
Target Market(s)
Anyone who needs building work done
Contact Information for Business Card
This business card is for a construction company which strives to deliver excellent service and quality.
The look and feel of the card should represent this.
Requirements
Must have
- On the first side what is needed are:
Logo
My name - Tomasz Brelwik
Title - Managing Director
Website - www.varkelt.co.uk
Email - tomasz@varkelt.co.uk
Telephone - 020 5194 6281
Mobile - 07845139072
Nice to have
- Cool looking features

```html
<!DOCTYPE html>
<html lang="en">
<head>
<meta charset="utf-8">
<title>Varkelt Construction Ltd – Business Card</title>
<link rel="stylesheet" href="https://fonts.googleapis.com/css2?family=Montserrat:wght@500;700&family=Open+Sans:wght@400&display=swap">
<style>
  :root {
    --stage: #4a4a4a;
    --black: #0d0d0d;
    --black-soft: #1c1c1c;
    --green: #6cb84a;
    --green-light: #7cc455;
    --green-dark: #3f7f34;
    --white: #ffffff;
    --text-light: #e9f3e3;
  }
  * { margin: 0; padding: 0; box-sizing: border-box; }
  html, body { width: 1200px; height: 982px; overflow: hidden; }
  body {
    background: var(--stage);
    position: relative;
    font-family: "Open Sans", Arial, sans-serif;
  }
  .card {
    position: absolute;
    left: 303px;
    width: 622px;
    height: 358px;
    border-radius: 30px;
    overflow: hidden;
    box-shadow: 0 6px 14px rgba(0,0,0,0.35);
  }
  .card svg.card-art { position: absolute; inset: 0; }

  /* Services side */
  .card--services { top: 112px; background: var(--black); }
  .brand {
    position: absolute;
    color: var(--green);
    font-family: "Montserrat", Arial, sans-serif;
    font-weight: 700;
    text-align: center;
    line-height: 1;
  }
  .brand__name { display: block; font-size: 46px; letter-spacing: 1px; }
  .brand__sub { display: block; font-size: 13px; letter-spacing: 2.6px; margin-top: 6px; }
  .card--services .brand { left: 0; width: 622px; top: 96px; }

  .services {
    position: absolute;
    top: 212px;
    list-style: none;
  }
  .services li {
    display: flex;
    align-items: center;
    height: 25.8px;
    font-size: 15.5px;
    color: var(--text-light);
    white-space: nowrap;
  }
  .services li svg { width: 17px; height: 17px; margin-right: 5px; flex: none; }
  .services--a { left: 27px; }
  .services--b { left: 260px; }
  .services--c { left: 438px; }

  /* Contact side */
  .card--contact {
    top: 513px;
    background: linear-gradient(135deg, var(--black-soft), var(--black) 70%);
  }
  .decor-mark {
    position: absolute;
    left: 40px; top: 20px;
    width: 330px; height: 310px;
    border-radius: 40px;
    background: radial-gradient(ellipse at center, rgba(70,110,60,0.16), rgba(70,110,60,0) 70%);
  }
  .person { position: absolute; left: 46px; top: 78px; font-family: "Montserrat", Arial, sans-serif; font-weight: 500; }
  .person__name { font-size: 21px; letter-spacing: 1.2px; color: var(--white); }
  .person__title { font-size: 15px; letter-spacing: 1.2px; color: var(--green); margin-top: 4px; }
  .card--contact .brand { left: 370px; width: 210px; top: 108px; }
  .card--contact .brand__name { font-size: 42px; }
  .card--contact .brand__sub { font-size: 11px; letter-spacing: 2px; }
  .divider {
    position: absolute; top: 152px; height: 4px; background: var(--green);
  }
  .divider--left { left: 0; width: 370px; }
  .divider--right { left: 584px; width: 38px; }

  .contact-list { position: absolute; top: 266px; list-style: none; font-size: 15.5px; color: var(--white); }
  .contact-list li { display: flex; align-items: center; height: 26px; gap: 7px; }
  .contact-list svg { width: 14px; height: 14px; flex: none; }
  .contact-list--left { left: 46px; }
  .contact-list--right { right: 46px; text-align: right; }
  .contact-list--right li { justify-content: flex-end; gap: 10px; }

  .web-band {
    position: absolute; left: 0; bottom: 0; width: 100%; height: 30px;
    background: linear-gradient(90deg, var(--green-light), var(--green));
    color: var(--white);
    font-family: "Montserrat", Arial, sans-serif;
    font-weight: 500;
    font-size: 15px;
    letter-spacing: 2px;
    text-align: center;
    line-height: 30px;
  }
</style>
</head>
<body>

<svg width="0" height="0" style="position:absolute">
  <defs>
    <symbol id="tick" viewBox="0 0 20 20">
      <circle cx="10" cy="10" r="8.3" fill="none" stroke="currentColor" stroke-width="1.6"/>
      <path d="M5.8 10.2l3 3 6.5-7" fill="none" stroke="currentColor" stroke-width="2" stroke-linecap="round" stroke-linejoin="round"/>
    </symbol>
    <symbol id="phone" viewBox="0 0 24 24">
      <path fill="#6cb84a" d="M6.6 10.8a15 15 0 0 0 6.6 6.6l2.2-2.2c.3-.3.7-.4 1-.2 1.1.4 2.3.6 3.6.6.6 0 1 .4 1 1V20c0 .6-.4 1-1 1A17 17 0 0 1 3 4c0-.6.4-1 1-1h3.5c.6 0 1 .4 1 1 0 1.3.2 2.5.6 3.6.1.3 0 .7-.2 1z"/>
    </symbol>
    <symbol id="mobile" viewBox="0 0 24 24">
      <rect x="6" y="2" width="12" height="20" rx="2" fill="none" stroke="#6cb84a" stroke-width="2.2"/>
      <circle cx="12" cy="18.5" r="1.2" fill="#6cb84a"/>
    </symbol>
    <symbol id="mail" viewBox="0 0 24 24">
      <rect x="2" y="5" width="20" height="14" rx="1.5" fill="#6cb84a"/>
      <path d="M2.5 6l9.5 7 9.5-7" fill="none" stroke="#0d0d0d" stroke-width="1.6"/>
    </symbol>
    <symbol id="globe" viewBox="0 0 24 24">
      <circle cx="12" cy="12" r="9.5" fill="#6cb84a"/>
      <path d="M2.5 12h19M12 2.5c-3 3-3 16 0 19M12 2.5c3 3 3 16 0 19M4 7h16M4 17h16" fill="none" stroke="#0d0d0d" stroke-width="1.3"/>
    </symbol>
  </defs>
</svg>

<section class="card card--services" aria-label="Services side">
  <svg class="card-art" width="622" height="358" viewBox="0 0 622 358" aria-hidden="true">
    <defs>
      <linearGradient id="greenFill" x1="0" y1="0" x2="1" y2="1">
        <stop offset="0" stop-color="#6bb34d"/>
        <stop offset="1" stop-color="#74c043"/>
      </linearGradient>
    </defs>
    <path d="M0 146 Q300 220 622 150 L622 358 L0 358 Z" fill="url(#greenFill)"/>
    <path d="M32 152 Q300 218 592 150 Q300 204 32 152 Z" fill="#0d0d0d"/>
    <path d="M60 162 Q300 212 590 152 Q320 226 60 162 Z" fill="#3f7f34"/>
  </svg>

  <div class="brand">
    <span class="brand__name">VARKELT</span>
    <span class="brand__sub">CONSTRUCTION LTD</span>
  </div>

  <ul class="services services--a">
    <li><svg><use href="#tick" color="#e9f3e3"/></svg>Kitchen Renovations</li>
    <li><svg><use href="#tick" color="#e9f3e3"/></svg>Bathroom Renovations</li>
    <li><svg><use href="#tick" color="#e9f3e3"/></svg>House Renovations</li>
    <li><svg><use href="#tick" color="#e9f3e3"/></svg>Garage Conversions</li>
    <li><svg><use href="#tick" color="#e9f3e3"/></svg>Extensions</li>
  </ul>
  <ul class="services services--b">
    <li><svg><use href="#tick" color="#e9f3e3"/></svg>Loft Conversions</li>
    <li><svg><use href="#tick" color="#e9f3e3"/></svg>Conservatories</li>
    <li><svg><use href="#tick" color="#e9f3e3"/></svg>Carpentry</li>
    <li><svg><use href="#tick" color="#e9f3e3"/></svg>Tiling</li>
    <li><svg><use href="#tick" color="#e9f3e3"/></svg>Electrical</li>
  </ul>
  <ul class="services services--c">
    <li><svg><use href="#tick" color="#e9f3e3"/></svg>Plumbing &amp; Heating</li>
    <li><svg><use href="#tick" color="#e9f3e3"/></svg>Bricklaying</li>
    <li><svg><use href="#tick" color="#e9f3e3"/></svg>Landscaping</li>
    <li><svg><use href="#tick" color="#e9f3e3"/></svg>Decorating</li>
    <li><svg><use href="#tick" color="#e9f3e3"/></svg>Plastering</li>
  </ul>
</section>

<section class="card card--contact" aria-label="Contact side">
  <div class="decor-mark" role="img" aria-label="Faint enlarged company emblem as background decoration"></div>

  <div class="person">
    <p class="person__name">TOMASZ BRELWIK</p>
    <p class="person__title">MANAGING DIRECTOR</p>
  </div>

  <div class="divider divider--left"></div>
  <div class="divider divider--right"></div>

  <div class="brand">
    <span class="brand__name">VARKELT</span>
    <span class="brand__sub">CONSTRUCTION LTD</span>
  </div>

  <ul class="contact-list contact-list--left">
    <li><svg><use href="#phone"/></svg>020 5194 6281</li>
    <li><svg><use href="#mobile"/></svg>07845139072</li>
  </ul>
  <ul class="contact-list contact-list--right">
    <li>tomasz@varkelt.co.uk<svg><use href="#mail"/></svg></li>
    <li>www.varkelt.co.uk<svg><use href="#globe"/></svg></li>
  </ul>

  <div class="web-band">WWW.VARKELT.CO.UK</div>
</section>

</body>
</html>
```